Telecommunications/Power civil contractor needs business card design

Were a new telecommunications/power underground civil contractor that is looking for a new business card design. Our company colours are silver or grey and orange. Feel free to use the white background logo or the black background logo.

Target Market(s)

Local contractors, utility companies, private sector mining/energy companies, developers.

Industry/Entity Type

Telecommunications

Contact Information for Business Card

Each card will need the following info:
Persons name:
Title:
E-mail:
Phone number:
Shop Address:
Mailing Address:

Requirements
Must have
• Each card will need the following info:
• Persons name:
• Title:
• E-mail:
• Phone number:
• Shop Address:
• Mailing Address:

```html
<!DOCTYPE html>
<html lang="en">
<head>
<meta charset="UTF-8">
<title>Ridgeline Contracting Inc – Business Card</title>
<link href="https://fonts.googleapis.com/css2?family=Source+Sans+3:wght@400;600;700&display=swap" rel="stylesheet">
<style>
  :root {
    --stage-top: #2b2b2b;
    --stage-bottom: #050505;
    --card: #ffffff;
    --orange: #f05a22;
    --grey: #5a5a5a;
    --grey-brand: #6b6b6b;
  }
  * { margin: 0; padding: 0; box-sizing: border-box; }
  html, body { width: 1200px; height: 900px; overflow: hidden; }
  body {
    position: relative;
    background: linear-gradient(180deg, var(--stage-top) 0%, #161616 55%, var(--stage-bottom) 100%);
    font-family: "Source Sans 3", sans-serif;
  }
  .card {
    position: absolute;
    top: 306px;
    width: 440px;
    height: 271px;
    background: var(--card);
    border-radius: 12px;
  }
  .card--front { left: 149px; }
  .card--back { left: 608px; }

  .brand-dot {
    flex: none;
    border-radius: 50%;
    background: var(--orange);
  }
  .brand-name {
    font-weight: 700;
    color: var(--grey-brand);
    letter-spacing: 0.5px;
  }

  .front-brand {
    position: absolute;
    left: 48px;
    top: 118px;
    display: flex;
    align-items: center;
    gap: 8px;
  }
  .front-brand .brand-dot { width: 14px; height: 14px; }
  .front-brand .brand-name { font-size: 25px; line-height: 32px; }

  .contact {
    position: absolute;
    left: 237px;
    top: 44px;
    color: var(--grey);
    font-size: 12.5px;
    line-height: 16px;
  }
  .contact-name {
    color: var(--orange);
    font-weight: 600;
    font-size: 15.5px;
    line-height: 18px;
  }
  .contact-title {
    font-size: 11.5px;
    line-height: 15px;
    margin-bottom: 1px;
  }
  .contact-line { display: flex; align-items: center; gap: 6px; }
  .contact-line svg { width: 9px; height: 9px; fill: var(--orange); }
  .section-title {
    color: var(--orange);
    font-weight: 600;
    font-size: 14px;
    margin-top: 14px;
    line-height: 17px;
  }
  .section-title--tight { margin-top: 5px; }

  .back-brand {
    position: absolute;
    left: 0; right: 0;
    top: 56px;
    display: flex;
    flex-direction: column;
    align-items: center;
    gap: 30px;
  }
  .back-brand .brand-dot { width: 90px; height: 90px; }
  .back-brand .brand-name {
    font-size: 20px;
    text-align: center;
    line-height: 22px;
  }
</style>
</head>
<body>
  <section class="card card--front">
    <div class="front-brand">
      <span class="brand-dot"></span>
      <span class="brand-name">RIDGELINE</span>
    </div>
    <div class="contact">
      <p class="contact-name">Daniel Carter</p>
      <p class="contact-title">Operations Manager</p>
      <p class="contact-line">
        <svg viewBox="0 0 10 10" aria-hidden="true"><path d="M2 0.5 L3.6 2.6 L2.8 3.6 C3.4 5 4.8 6.5 6.4 7.2 L7.4 6.4 L9.5 8 L8.4 9.5 C4.5 9.2 0.8 5.5 0.5 1.6 Z"/></svg>
        044-555 010 220
      </p>
      <p class="contact-line">
        <svg viewBox="0 0 10 10" aria-hidden="true"><path d="M0.5 2 H9.5 V8.5 H0.5 Z M1.2 2.6 L5 5.4 L8.8 2.6"/></svg>
        info@ridgelinecivil.com
      </p>
      <p class="section-title">Shop Address</p>
      <p>12345, Address Goes Here</p>
      <p>Country Name, 123456.</p>
      <p class="section-title section-title--tight">Mailing Address</p>
      <p>12345, Address Goes Here</p>
      <p>Country Name, 123456.</p>
    </div>
  </section>

  <section class="card card--back">
    <div class="back-brand">
      <span class="brand-dot"></span>
      <span class="brand-name">RIDGELINE<br>CONTRACTING INC</span>
    </div>
  </section>
</body>
</html>
```